Spy/Espionage/Counterintelligence Membership Community Needs a PowerPoint Template

We need a powerpoint template for one of our business verticals focused on spies, espionage, and counterintelligence. The name of it is "Brass Lantern Guild" and the logo is attached. Brass Lantern Guild is a community that connects people with experts in espionage and counterintelligence through an online social network, as well as in-person events. We would like to see designs that incorporate the red and black of the logo. The design should communicate mystery/suspense and peak curiosity.

Target Market(s)

Late 20s to baby boomers, male

Industry/Entity Type

Social Club

Font styles to use
Sans Serif

Colors
ec1f27
000000
ffffff

Requirements
Must have
• A user-friendly ppt template file. Incorporate basic fonts that don't have to be installed on every computer for presentations. A cover slide and a basic inside slide. A white background. I will also need graphic source files.
Nice to have
• Plenty of space for slide title and body content. Logo on every slide.
Should not have
• Inconsistency with fonts. Misalignment of images.

```html
<!DOCTYPE html>
<html lang="en">
<head>
<meta charset="utf-8">
<title>Brass Lantern Guild – Slide Template</title>
<link href="https://fonts.googleapis.com/css2?family=Questrial&family=Roboto:wght@400;700&display=swap" rel="stylesheet">
<style>
  :root {
    --brand-red: #c8070b;
    --accent-red: #ec1f27;
    --wine: #7f141c;
    --crimson: #a8181e;
    --scarlet: #d4242a;
    --slate: #8fa3a5;
    --charcoal: #3d3d3d;
    --navy-grey: #4a4c63;
    --ink: #111111;
    --body-text: #222222;
    --panel: #f5f7fc;
    --ghost: #ececec;
    --footer: #161616;
    --white: #ffffff;
  }
  * { margin: 0; padding: 0; box-sizing: border-box; }
  html, body { width: 1200px; height: 900px; overflow: hidden; background: var(--white); }
  .slide { position: relative; width: 1200px; height: 900px; overflow: hidden; background: var(--white); font-family: "Roboto", Arial, sans-serif; }

  .slide-header { position: absolute; left: 0; top: 0; width: 1200px; height: 72px; background: var(--brand-red); border-bottom: 4px solid #3a0b0b; }
  .slide-title { position: absolute; left: 18px; top: 12px; font-family: "Questrial", "Century Gothic", sans-serif; font-size: 42px; color: var(--white); font-weight: 400; letter-spacing: 0.3px; }
  .brand { position: absolute; right: 18px; top: 14px; display: flex; align-items: center; gap: 10px; }
  .brand-dot { width: 40px; height: 40px; border-radius: 50%; background: var(--ink); }
  .brand-name { font-family: "Questrial", "Century Gothic", sans-serif; font-size: 30px; color: var(--ink); }

  .diagram { position: absolute; left: 0; top: 0; }

  .info-panel { position: absolute; left: 963px; top: 112px; width: 170px; height: 720px; background: var(--panel); }

  .note { position: absolute; width: 260px; }
  .note h2 { font-size: 24px; font-weight: 700; line-height: 1.2; margin-bottom: 4px; }
  .note p { font-size: 18.5px; line-height: 27px; color: var(--body-text); }
  .note--red h2 { color: var(--brand-red); }
  .note--grey h2 { color: var(--navy-grey); }
  .note--right { text-align: right; }

  .hub-label { position: absolute; left: 536px; top: 381px; width: 124px; height: 124px; display: flex; align-items: center; justify-content: center; text-align: center; font-size: 17px; font-weight: 700; line-height: 1.2; color: var(--brand-red); }

  .slide-footer { position: absolute; left: 0; bottom: 0; width: 1200px; height: 44px; background: var(--footer); }
  .copyright { position: absolute; left: 10px; top: 10px; font-size: 21px; color: var(--white); }
  .page-number { position: absolute; right: 10px; top: 5px; width: 34px; height: 34px; border-radius: 50%; background: var(--brand-red); border: 2px solid var(--white); color: var(--white); font-size: 18px; display: flex; align-items: center; justify-content: center; }
</style>
</head>
<body>
<div class="slide">

  <svg class="diagram" width="1200" height="900" viewBox="0 0 1200 900" aria-hidden="true">
    <circle cx="180" cy="450" r="315" fill="var(--ghost)"/>
  </svg>

  <div class="info-panel"></div>

  <svg class="diagram" width="1200" height="900" viewBox="0 0 1200 900" aria-hidden="true">
    <g fill="none" stroke-width="33">
      <path d="M619.8 193.9 A250 250 0 0 1 758.7 251.5" stroke="var(--crimson)"/>
      <path d="M789.5 282.3 A250 250 0 0 1 847.9 434.3" stroke="var(--scarlet)"/>
      <path d="M847.0 464.8 A250 250 0 0 1 789.5 603.7" stroke="var(--slate)"/>
      <path d="M765.3 628.8 A250 250 0 0 1 619.8 692.1" stroke="var(--charcoal)"/>
      <path d="M576.2 692.1 A250 250 0 0 1 437.3 634.5" stroke="var(--navy-grey)"/>
      <path d="M406.5 603.7 A250 250 0 0 1 348.9 464.8" stroke="var(--ink)"/>
      <path d="M348.9 421.2 A250 250 0 0 1 406.5 282.3" stroke="var(--ink)"/>
      <path d="M437.3 251.5 A250 250 0 0 1 576.2 193.9" stroke="var(--wine)"/>
    </g>
    <g fill="none" stroke-width="3">
      <polyline points="248,218 327,218 393,278" stroke="var(--ink)"/>
      <polyline points="248,474 323,474 366,512" stroke="var(--ink)"/>
      <polyline points="248,716 368,716 435,652" stroke="var(--navy-grey)"/>
      <polyline points="773,237 830,177 963,177" stroke="var(--crimson)"/>
      <polyline points="868,422 952,422" stroke="var(--scarlet)"/>
      <polyline points="780,600 867,680 963,680" stroke="var(--slate)"/>
    </g>
    <circle cx="598" cy="443" r="62" fill="var(--white)" stroke="var(--accent-red)" stroke-width="4"/>
  </svg>

  <div class="hub-label">Brass Lantern Guild</div>

  <header class="slide-header">
    <h1 class="slide-title">Project Title Here</h1>
    <div class="brand">
      <span class="brand-dot"></span>
      <span class="brand-name">Brass Lantern Guild</span>
    </div>
  </header>

  <div class="note note--red" style="left:60px; top:200px;">
    <h2>Heading Here</h2>
    <p>Subtext here Subtext here Sub-text here Subtext here Subtext here Subtext here</p>
  </div>
  <div class="note note--red" style="left:60px; top:462px;">
    <h2>Heading Here</h2>
    <p>Subtext here Subtext here Sub-text here Subtext here Subtext here Subtext here</p>
  </div>
  <div class="note note--grey" style="left:61px; top:694px; width:200px;">
    <h2>Heading Here</h2>
    <p>Subtext here Subtext here Subtext here Sub-text here Subtext here Subtext here</p>
  </div>

  <div class="note note--grey note--right" style="left:865px; top:162px;">
    <h2>Heading Here</h2>
    <p>Subtext here Subtext here Sub-text here Subtext here Subtext here Subtext here</p>
  </div>
  <div class="note note--grey note--right" style="left:880px; top:404px;">
    <h2>Heading Here</h2>
    <p>Subtext here Subtext here Sub-text here Subtext here Subtext here Subtext here</p>
  </div>
  <div class="note note--grey" style="left:876px; top:664px; width:260px;">
    <h2 style="text-align:right; width:249px;">Heading Here</h2>
    <p>Subtext here Subtext here Sub-text here Subtext here Subtext here Subtext here</p>
  </div>

  <footer class="slide-footer">
    <span class="copyright">Copyright text here</span>
    <span class="page-number">1</span>
  </footer>
</div>
</body>
</html>
```